Velvet Riot Rising Line of Sparkling Wine & Spirits

Back info: Nora Beth Quill Owner 555-318-4402 1480 E. Harlow Ave, Bldg. 2, & 3, Fenwick Ca. 95871
Sparkling Wines & Memorabilia www.velvetriotrising.com
Ok I have uploaded the winning design. The color that I am after is the Fushia, Raspberry, Red, Matte Satin Matalic Finish. With a 24 Karet Gold color Foil. The Bottle is on the top row and it's the 2nd Bottle in. That is the Color that I want. This is the style of font. Make sure that you put what we're advertising. Good Luck to you all. Warmest regards, Nora
21 & up UniSex
Sparkling Wine and Memorabilia
there listed up above.....

```html
<!DOCTYPE html>
<html lang="en">
<head>
<meta charset="utf-8">
<title>Velvet Riot Rising — Business Card</title>
<link rel="stylesheet" href="https://fonts.googleapis.com/css2?family=Cinzel:wght@400;600&display=swap">
<style>
  :root {
    --stage: #3a3a3c;
    --fuchsia: #dc148c;
    --fuchsia-deep: #9c0f58;
    --gold: #c9a23c;
    --gold-light: #e8c86a;
    --ink: #1d1d1f;
    --white: #ffffff;
  }
  * { box-sizing: border-box; margin: 0; padding: 0; }
  html, body {
    width: 1200px; height: 1200px; overflow: hidden;
    background: var(--stage);
    font-family: "Cinzel", serif;
  }
  .card {
    position: absolute;
    left: 170px;
    width: 860px; height: 491px;
    border-radius: 34px;
    overflow: hidden;
    background: linear-gradient(120deg, var(--fuchsia-deep) 0%, var(--fuchsia) 40%, var(--fuchsia) 60%, var(--fuchsia-deep) 100%);
    border: 3px solid var(--gold);
  }
  .card--front { top: 80px; }
  .card--back { top: 630px; }

  .identity { position: absolute; left: 60px; top: 58px; }
  .identity__name { color: var(--gold); font-size: 34px; font-weight: 600; letter-spacing: 1px; }
  .identity__role { color: var(--white); font-size: 22px; margin-top: 2px; }

  .contact { position: absolute; left: 60px; top: 160px; list-style: none; color: var(--white); font-size: 17px; line-height: 1.35; }
  .contact li { display: flex; align-items: flex-start; gap: 12px; margin-bottom: 6px; }
  .contact svg { width: 18px; height: 18px; flex: none; margin-top: 2px; fill: var(--gold); }

  .wordmark {
    position: absolute;
    color: var(--gold);
    font-weight: 600;
    text-align: center;
    line-height: 1.05;
  }
  .card--front .wordmark { right: 56px; top: 70px; font-size: 30px; width: 300px; }
  .card--back .wordmark { left: 0; right: 0; top: 50%; transform: translateY(-50%); font-size: 56px; }

  .gold-rule { position: absolute; left: 0; right: 0; top: 340px; height: 12px; background: linear-gradient(90deg, var(--gold), var(--gold-light), var(--gold)); }
  .pattern-band { position: absolute; left: 0; right: 0; top: 352px; bottom: 0; background: linear-gradient(90deg, #3a1028, #2a1420, #3a1028); }
</style>
</head>
<body>
  <section class="card card--front">
    <div class="identity">
      <h1 class="identity__name">Nora Beth Quill</h1>
      <p class="identity__role">Owner</p>
    </div>
    <ul class="contact">
      <li>
        <svg viewBox="0 0 24 24"><path d="M6.6 10.8a15.1 15.1 0 0 0 6.6 6.6l2.2-2.2c.3-.3.7-.4 1-.2 1.1.4 2.3.6 3.6.6.6 0 1 .4 1 1V20c0 .6-.4 1-1 1A17 17 0 0 1 3 4c0-.6.4-1 1-1h3.5c.6 0 1 .4 1 1 0 1.3.2 2.5.6 3.6.1.3 0 .7-.2 1z"/></svg>
        <span>555-318-4402</span>
      </li>
      <li>
        <svg viewBox="0 0 24 24"><path d="M12 2a10 10 0 1 0 0 20 10 10 0 0 0 0-20zm6.9 6h-3a15.6 15.6 0 0 0-1.4-3.6A8 8 0 0 1 18.9 8zM12 4c.8 1.2 1.5 2.5 1.9 4h-3.8c.4-1.5 1.1-2.8 1.9-4zM4.3 14a8 8 0 0 1 0-4h3.4a16 16 0 0 0 0 4zm.8 2h3a15.6 15.6 0 0 0 1.4 3.6A8 8 0 0 1 5.1 16zM8 8H5.1a8 8 0 0 1 4.4-3.6C8.9 5.5 8.4 6.7 8 8zm4 12c-.8-1.2-1.5-2.5-1.9-4h3.8c-.4 1.5-1.1 2.8-1.9 4zm2.3-6H9.7a14 14 0 0 1 0-4h4.6a14 14 0 0 1 0 4zm.3 5.6c.6-1.1 1.1-2.3 1.4-3.6h3a8 8 0 0 1-4.4 3.6zm1.7-5.6a16 16 0 0 0 0-4h3.4a8 8 0 0 1 0 4z"/></svg>
        <span>www.velvetriotrising.com</span>
      </li>
      <li>
        <svg viewBox="0 0 24 24"><path d="M12 2a7 7 0 0 0-7 7c0 5.2 7 13 7 13s7-7.8 7-13a7 7 0 0 0-7-7zm0 9.5a2.5 2.5 0 1 1 0-5 2.5 2.5 0 0 1 0 5z"/></svg>
        <span>1480 E. Harlow Ave, Bldg. 2, &amp; 3,<br>Fenwick Ca. 95871<br>Sparkling Wines &amp; Memorabilia</span>
      </li>
    </ul>
    <p class="wordmark">Velvet Riot Rising</p>
    <div class="gold-rule"></div>
    <div class="pattern-band" role="img" aria-label="Decorative lattice pattern band in black and fuchsia"></div>
  </section>

  <section class="card card--back">
    <p class="wordmark">Velvet Riot Rising</p>
  </section>
</body>
</html>
```